Home Staging Company needs business card design

We're a home staging company called Brightly Settled Home Staging. We would like a business card design that includes aqua and gray. Our current logo of house within chair is fine but I find we almost always use the logo in one color. I'll upload images of front and back of our current card and our logo. Note that we have dropped "Solutions" from our company name and don't want to include it on the card.

Target Market(s)

Realtors and homeowners - people interested in selling their homes

Contact Information for Business Card

Marisol Thistlewood
Brightly Settled Home Staging
757-555-0193
www.brightlysettled.com
marisol@brightlysettled.com

Font styles to use
Serif
Script

Requirements
Must have
• My logo and contact details
• UPDATE***
• I forgot to say that the company name should be included on the front of the card somehow.

```html
<!DOCTYPE html>
<html lang="en">
<head>
<meta charset="utf-8">
<title>Brightly Settled Home Staging – Business Card</title>
<link rel="stylesheet" href="https://fonts.googleapis.com/css2?family=Playfair+Display:wght@700&family=Roboto:wght@400&display=swap">
<style>
  :root {
    --stage: #111111;
    --charcoal: #3b3b3d;
    --charcoal-dark: #2f2f31;
    --ink: #2c2c2e;
    --slate: #454547;
    --aqua: #6ac8ca;
    --aqua-light: #94d7d8;
    --silver: #d3d3d5;
    --paper: #ffffff;
    --serif: "Playfair Display", Georgia, serif;
    --sans: "Roboto", Arial, sans-serif;
  }
  * { margin: 0; padding: 0; box-sizing: border-box; }
  html, body { width: 1200px; height: 1000px; overflow: hidden; background: var(--stage); }
  .canvas { position: relative; width: 1200px; height: 1000px; }

  .card {
    position: absolute;
    width: 520px;
    height: 300px;
    border-radius: 24px;
    overflow: hidden;
  }

  /* Back of card */
  .card-back { left: 60px; top: 220px; }
  .card-back .texture {
    position: absolute; inset: 0;
    background: linear-gradient(135deg, var(--charcoal) 0%, var(--charcoal-dark) 100%);
  }
  .card-back .brand-mark {
    position: absolute; left: 0; right: 0; top: 118px;
    display: flex; align-items: center; justify-content: center; gap: 12px;
  }
  .card-back .brand-square {
    width: 18px; height: 18px; background: var(--aqua);
  }
  .card-back .brand-name {
    font-family: var(--serif); font-weight: 700; font-size: 22px;
    color: var(--paper);
  }
  .card-back .website {
    position: absolute; left: 36px; bottom: 34px;
    font-family: var(--sans); font-size: 17px; letter-spacing: 2px;
    color: var(--paper);
  }

  /* Front of card */
  .card-front { left: 620px; top: 470px; background: var(--paper); }
  .card-front svg.shapes { position: absolute; inset: 0; }
  .contact { position: absolute; left: 28px; top: 26px; }
  .contact .person {
    font-family: var(--serif); font-weight: 700; font-size: 26px;
    color: var(--ink); margin-bottom: 8px;
  }
  .contact .detail {
    font-family: var(--sans); font-size: 15px; line-height: 20px;
    color: var(--ink);
  }
  .front-brand {
    position: absolute; left: 40px; top: 186px;
    display: flex; align-items: center; gap: 14px;
  }
  .front-brand .brand-square { width: 34px; height: 34px; background: var(--slate); flex: none; }
  .front-brand .brand-name {
    font-family: var(--serif); font-weight: 700; font-size: 26px; line-height: 30px;
    color: var(--slate);
  }
  .front-brand .brand-line { display: block; white-space: nowrap; }
</style>
</head>
<body>
<main class="canvas">

  <section class="card card-back" aria-label="Card back">
    <div class="texture" role="img" aria-label="Subtle diamond lattice pattern on charcoal"></div>
    <div class="brand-mark">
      <span class="brand-square"></span>
      <span class="brand-name">Brightly Settled Home Staging</span>
    </div>
    <p class="website">www.brightlysettled.com</p>
  </section>

  <section class="card card-front" aria-label="Card front">
    <svg class="shapes" width="520" height="300" viewBox="0 0 520 300" aria-hidden="true">
      <defs>
        <linearGradient id="aquaWash" x1="0" y1="0" x2="1" y2="0.4">
          <stop offset="0" stop-color="var(--aqua)"/>
          <stop offset="0.3" stop-color="var(--aqua-light)"/>
          <stop offset="1" stop-color="var(--aqua)"/>
        </linearGradient>
      </defs>
      <polygon points="0,118 520,168 520,300 0,300" fill="url(#aquaWash)"/>
      <circle cx="540" cy="120" r="128" fill="var(--paper)"/>
      <circle cx="540" cy="120" r="116" fill="var(--slate)"/>
      <circle cx="540" cy="120" r="104" fill="var(--paper)"/>
      <circle cx="540" cy="120" r="96" fill="var(--silver)"/>
      <line x1="0" y1="118" x2="432" y2="160" stroke="var(--slate)" stroke-width="3" stroke-dasharray="7 5"/>
    </svg>
    <div class="contact">
      <h1 class="person">Marisol Thistlewood</h1>
      <p class="detail">757-555-0193</p>
      <p class="detail">marisol@brightlysettled.com</p>
    </div>
    <div class="front-brand">
      <span class="brand-square"></span>
      <span class="brand-name">
        <span class="brand-line">Brightly Settled</span>
        <span class="brand-line">Home Staging</span>
      </span>
    </div>
  </section>

</main>
</body>
</html>
```